R. Talmont Realty, Inc business card (2 sided), letterhead (1 sided) & #10 envelope (1 sided)

business card of standard size utilizing the attached logo. Side one with logo, Owen Talmont (my name), President / Broker (title), 805-317-2684 (phone), www.rtalmontrealty.example (website), 1726 Harlow Avenue, Suite 4052 San Luis Obiso, CA 93628 (business address) owen.rtalmontrealty@mailbox.example (e-mail address),
Side two - Log

Letterhead and #10 envelope in the same theme
Updates

Project Deadline Extended
Reason: I think a 2 day deadline may be a bit ambitious on my part. I have extended the deadline to 4 days. Thanks!

Industry/Entity Type

Business

```html
<!DOCTYPE html>
<html lang="en">
<head>
<meta charset="utf-8">
<title>R. Talmont Realty, Inc – Business Card</title>
<link rel="stylesheet" href="https://fonts.googleapis.com/css2?family=Noto+Serif:wght@400;700&family=Open+Sans:wght@400&display=swap">
<style>
  :root {
    --backdrop: #e8e6e2;
    --card: #ffffff;
    --card-edge: #6f6f6f;
    --brand-blue: #17678f;
    --blue-light: #1d8fc6;
    --blue-dark: #0e4a68;
    --charcoal: #323233;
    --ink: #2b2b2b;
    --divider: #b5b5b5;
  }
  * { box-sizing: border-box; margin: 0; padding: 0; }
  html, body { width: 1200px; height: 1182px; overflow: hidden; }
  body { background: var(--backdrop); position: relative; font-family: "Open Sans", sans-serif; }

  .card {
    position: absolute;
    background: var(--card);
    border: 1px solid var(--card-edge);
    overflow: hidden;
  }
  .card--front { left: 29px; top: 25px; width: 969px; height: 561px; }
  .card--back  { left: 249px; top: 626px; width: 911px; height: 518px; }

  .brand {
    position: absolute;
    display: flex;
    align-items: center;
    gap: 14px;
    font-family: "Noto Serif", serif;
    font-weight: 400;
    color: var(--brand-blue);
    line-height: 1.15;
  }
  .brand__mark { width: 22px; height: 22px; background: var(--brand-blue); flex: none; }
  .card--front .brand { left: 70px; top: 170px; width: 420px; font-size: 40px; }
  .card--back .brand { left: 0; right: 0; top: 175px; justify-content: center; font-size: 50px; }

  .contact {
    position: absolute;
    left: 542px;
    top: 180px;
    padding-left: 18px;
    border-left: 1px solid var(--divider);
    list-style: none;
    color: var(--ink);
    font-size: 19px;
  }
  .contact__item { display: flex; align-items: center; gap: 8px; height: 41px; }
  .contact__icon { width: 17px; height: 17px; flex: none; }

  .swoosh { position: absolute; left: 0; top: 0; width: 969px; height: 561px; }

  .signature {
    position: absolute;
    left: 580px;
    width: 300px;
    top: 458px;
    text-align: center;
    color: #ffffff;
    font-family: "Noto Serif", serif;
  }
  .signature__name { font-size: 32px; font-weight: 700; line-height: 1.2; }
  .signature__title { font-size: 24px; font-weight: 400; line-height: 1.4; }

  .website {
    position: absolute;
    left: 0; right: 0; top: 432px;
    text-align: center;
    font-size: 26px;
    letter-spacing: 3px;
    color: var(--ink);
  }
</style>
</head>
<body>

<section class="card card--front" aria-label="Business card, front">
  <svg class="swoosh" viewBox="0 0 969 561" aria-hidden="true">
    <defs>
      <linearGradient id="band-gradient" x1="0" y1="0" x2="1" y2="0">
        <stop offset="0" stop-color="var(--blue-light)"/>
        <stop offset="1" stop-color="var(--blue-dark)"/>
      </linearGradient>
    </defs>
    <path d="M0,520 C200,540 330,500 430,468 C580,422 780,420 969,470 L969,561 L0,561 Z" fill="url(#band-gradient)"/>
    <path d="M0,432 C120,492 300,506 430,468 C580,424 780,414 969,462" fill="none" stroke="var(--charcoal)" stroke-width="11"/>
    <path d="M0,470 C150,515 300,515 420,488" fill="none" stroke="var(--blue-light)" stroke-width="7"/>
    <path d="M0,500 C160,540 320,520 440,480 C590,432 790,428 969,478" fill="none" stroke="#ffffff" stroke-width="3"/>
  </svg>

  <div class="brand"><span class="brand__mark"></span><span>R. Talmont Realty, Inc</span></div>

  <ul class="contact">
    <li class="contact__item">
      <svg class="contact__icon" viewBox="0 0 20 20" aria-hidden="true"><circle cx="10" cy="10" r="9" fill="none" stroke="var(--brand-blue)" stroke-width="2"/><path d="M7,5 L9,8 L8,9 C9,11 10,12 11,12 L12,11 L15,13 L13,15 C9,15 5,11 5,7 Z" fill="var(--brand-blue)"/></svg>
      <span>805-317-2684</span>
    </li>
    <li class="contact__item">
      <svg class="contact__icon" viewBox="0 0 20 20" aria-hidden="true"><circle cx="10" cy="10" r="10" fill="var(--brand-blue)"/><rect x="4.5" y="6.5" width="11" height="7" fill="#fff"/><path d="M4.5,6.5 L10,11 L15.5,6.5" fill="none" stroke="var(--brand-blue)" stroke-width="1.2"/></svg>
      <span>owen.rtalmontrealty@mailbox.example</span>
    </li>
    <li class="contact__item">
      <svg class="contact__icon" viewBox="0 0 20 20" aria-hidden="true"><circle cx="10" cy="10" r="9" fill="var(--brand-blue)"/><g fill="none" stroke="#fff" stroke-width="1.2"><ellipse cx="10" cy="10" rx="4" ry="9"/><line x1="1" y1="10" x2="19" y2="10"/><line x1="10" y1="1" x2="10" y2="19"/></g></svg>
      <span>www.rtalmontrealty.example</span>
    </li>
  </ul>

  <div class="signature">
    <p class="signature__name">Owen Talmont</p>
    <p class="signature__title">President / Broker</p>
  </div>
</section>

<section class="card card--back" aria-label="Business card, back">
  <div class="brand"><span class="brand__mark"></span><span>R. Talmont Realty, Inc</span></div>
  <p class="website">www.rtalmontrealty.example</p>
</section>

</body>
</html>
```